Maple n Brook - Contact/Landing Page

I need a landing page which will essentially be the page that customers will go to from the 'website' link on QTV listing. It will provide a short overview of services which need to be selectable. a little further down can capture some contact details followed by a large Submit Now button etc...

I have some icon/logo's that can be utilised at the bottom of the page as industry type references.

Target Market(s)

End of Lease Cleaning Services

Industry/Entity Type

Cleaning Service

Colors

Designer to choose colors to be used in the design.

Requirements
Must have
• As per description
Should not have
• Colours to match my website maplenbrook.com.au

```html
<!DOCTYPE html>
<html lang="en">
<head>
<meta charset="utf-8">
<title>Maple n Brook – End of Lease Cleaning</title>
<link rel="stylesheet" href="https://fonts.googleapis.com/css2?family=Poppins:wght@400;600;700&family=Lato:wght@400;700&family=Roboto:wght@300;400&display=swap">
<style>
:root{
  --brand:#457fc3;
  --brand-dark:#3a6fae;
  --pale:#e4ecf8;
  --ink:#111111;
  --muted:#333333;
  --white:#ffffff;
  --footer:#000000;
  --line:#222222;
}
*{box-sizing:border-box;margin:0;padding:0}
html,body{width:1200px;height:2793px;overflow:hidden}
body{position:relative;font-family:'Lato',sans-serif;color:var(--ink);background:var(--white)}
.abs{position:absolute}

/* hero */
.hero{position:absolute;left:0;top:0;width:1200px;height:600px;background:var(--brand)}
.menu-toggle{position:absolute;left:113px;top:40px;width:16px;height:13px;display:flex;flex-direction:column;justify-content:space-between}
.menu-toggle span{height:2px;background:var(--white)}
.hero-brand{position:absolute;left:0;top:180px;width:1200px;display:flex;flex-direction:column;align-items:center;gap:22px}
.hero-brand .mark{width:90px;height:90px;border-radius:50%;background:rgba(255,255,255,.25)}
.hero-brand .name{font-family:'Poppins',sans-serif;font-weight:700;font-size:56px;color:var(--white);letter-spacing:1px}
.tagline{position:absolute;left:0;top:480px;width:1200px;text-align:center;font-family:'Roboto',sans-serif;font-weight:300;font-size:36px;color:var(--white)}

/* section headings */
.section-title{position:absolute;left:0;width:1200px;text-align:center;font-family:'Poppins',sans-serif;font-weight:700;font-size:36px;color:var(--ink)}

/* services */
.service-card{position:absolute;top:791px;width:308px;height:445px;background:var(--white);box-shadow:0 2px 8px rgba(0,0,0,.15)}
.service-card .photo{height:226px}
.service-card h3{position:absolute;left:14px;top:252px;font-family:'Poppins',sans-serif;font-weight:700;font-size:22px;color:var(--ink)}
.service-card p{position:absolute;left:15px;top:296px;width:280px;font-size:15.5px;line-height:24px;color:var(--muted)}
.service-card .btn{position:absolute;left:14px;top:367px;width:142px;height:54px;border-radius:4px;background:var(--brand);color:var(--white);font-size:16px;display:flex;align-items:center;justify-content:center;text-decoration:none}
.photo-cleaning{background:linear-gradient(135deg,#c94a2c,#e9c35a 45%,#3d6fb8)}
.photo-carpet{background:linear-gradient(135deg,#9c9c98,#d2d0cc 55%,#b7b6b2)}
.photo-pest{background:linear-gradient(135deg,#cdb08a,#e6d3b4 50%,#b7874e)}

/* contact */
.contact{position:absolute;left:0;top:1331px;width:1200px;height:770px;background:var(--pale)}
.contact-icon{position:absolute;left:180px;top:1585px;width:342px;height:342px}
.field{position:absolute;left:636px;width:418px;height:49px;border:1px solid #c9d4e4;border-radius:25px;background:var(--white);font-family:'Poppins',sans-serif;font-size:15px;color:#777;padding:14px 0 0 28px}
.field.area{height:136px;border-radius:34px;padding-top:20px}
.submit{position:absolute;left:636px;top:1965px;width:418px;height:48px;border-radius:24px;background:var(--brand);color:var(--white);font-family:'Poppins',sans-serif;font-weight:700;font-size:15px;display:flex;align-items:center;justify-content:center}

/* partner strip */
.partner{position:absolute;top:2189px;width:226px;height:89px;background:var(--white);border-radius:6px;box-shadow:0 1px 8px rgba(0,0,0,.18);display:flex;align-items:center;justify-content:center}
.partner .badge{width:186px;height:54px;border-radius:4px}
.slider-arrow{position:absolute;top:2217px;width:32px;height:32px;border-radius:50%;background:var(--white);box-shadow:0 1px 5px rgba(0,0,0,.2);display:flex;align-items:center;justify-content:center}

/* footer */
.footer{position:absolute;left:0;top:2368px;width:1200px;height:425px;background:var(--footer);color:var(--white)}
.footer-brand{position:absolute;left:114px;top:70px;display:flex;align-items:center;gap:10px;font-family:'Poppins',sans-serif;font-weight:700;font-size:22px}
.footer-brand .mark{width:34px;height:34px;border-radius:50%;background:var(--brand)}
.footer-about{position:absolute;left:114px;top:172px;width:275px;font-family:'Poppins',sans-serif;font-size:15.5px;line-height:26px}
.footer h4{position:absolute;font-family:'Poppins',sans-serif;font-weight:700;font-size:16px}
.quick-links{position:absolute;left:474px;top:70px;list-style:none;font-size:15.5px;line-height:26px}
.quick-links li::before{content:"«";margin-right:10px}
.contact-list{position:absolute;left:655px;top:70px;font-size:15.5px;line-height:26px;list-style:none}
.contact-list li{display:flex;gap:8px;align-items:flex-start;margin-bottom:12px}
.contact-list svg{margin-top:6px;flex:none}
.social{position:absolute;left:912px;top:69px;display:flex;gap:8px}
.social span{width:35px;height:35px;border-radius:50%;background:var(--brand)}
.licence{position:absolute;left:916px;top:175px;font-family:'Poppins',sans-serif;font-size:15.5px}
.footer-rule{position:absolute;left:112px;top:322px;width:976px;height:1px;background:var(--line)}
.copyright{position:absolute;left:0;top:358px;width:1200px;text-align:center;font-family:'Poppins',sans-serif;font-size:15.5px}
</style>
</head>
<body>

<header class="hero">
  <div class="menu-toggle"><span></span><span></span><span></span><span></span></div>
  <div class="hero-brand">
    <div class="mark"></div>
    <div class="name">Maple n Brook</div>
  </div>
  <p class="tagline">End of Lease Cleaning I Licensed pest Control</p>
</header>

<h2 class="section-title" style="top:676px">OUR SERVICES</h2>

<article class="service-card" style="left:112px">
  <div class="photo photo-cleaning" role="img" aria-label="Cleaning supplies, mop and broom with a House Cleaning label"></div>
  <h3>CLEANING</h3>
  <p>All Interior cleaning carried out to property management Requirements</p>
  <a class="btn" href="#">LEARN MORE</a>
</article>
<article class="service-card" style="left:444px">
  <div class="photo photo-carpet" role="img" aria-label="Vacuum cleaner head on grey carpet"></div>
  <h3>CARPET CLEANING</h3>
  <p>Carpet Steam cleaning to australian Standard AS 3733:1995</p>
  <a class="btn" href="#">LEARN MORE</a>
</article>
<article class="service-card" style="left:777px">
  <div class="photo photo-pest" role="img" aria-label="Cockroach on a floor with a Pest Control label"></div>
  <h3>PEST CONTROL</h3>
  <p>Mandatory requirement for pets on premises</p>
  <a class="btn" href="#">LEARN MORE</a>
</article>

<section class="contact"></section>
<h2 class="section-title" style="top:1410px">CONTACT US</h2>
<svg class="contact-icon" viewBox="0 0 342 342" aria-hidden="true">
  <path d="M12 130 L150 18 Q171 2 192 18 L330 130 V318 H12 Z" fill="none" stroke="var(--brand)" stroke-width="24" stroke-linejoin="round"/>
  <path d="M64 176 L145 238 Q171 258 197 238 L278 176" fill="none" stroke="var(--brand)" stroke-width="24" stroke-linecap="round" stroke-linejoin="round"/>
</svg>
<div class="field" style="top:1518px">First Name</div>
<div class="field" style="top:1588px">Surname</div>
<div class="field" style="top:1658px">Email</div>
<div class="field" style="top:1728px">phone</div>
<div class="field area" style="top:1804px">Suburb</div>
<div class="submit">SUBMIT</div>

<div class="slider-arrow" style="left:32px"><svg width="8" height="10" viewBox="0 0 8 10"><path d="M6 1 L2 5 L6 9" fill="none" stroke="#333" stroke-width="1.5"/></svg></div>
<div class="partner" style="left:117px"><div class="badge" style="background:#8db548"></div></div>
<div class="partner" style="left:363px"><div class="badge" style="background:#111"></div></div>
<div class="partner" style="left:609px"><div class="badge" style="background:#2b4ea0;width:110px"></div></div>
<div class="partner" style="left:855px"><div class="badge" style="background:#c9333a"></div></div>
<div class="slider-arrow" style="left:1125px"><svg width="8" height="10" viewBox="0 0 8 10"><path d="M2 1 L6 5 L2 9" fill="none" stroke="#333" stroke-width="1.5"/></svg></div>

<footer class="footer">
  <div class="footer-brand"><span class="mark"></span>Maple n Brook</div>
  <p class="footer-about">Lorem ipsum dolor sit amet, consectetur adipiscing elit, sed do eiusmod tempor incididunt ut labore et dolore magna aliqua.</p>

  <h4 style="left:466px;top:38px">QUICK LINK</h4>
  <ul class="quick-links" style="top:80px">
    <li>Home</li><li>About</li><li>Cleaning</li><li>Carpets</li><li>Windows</li><li>Pest Control</li><li>Tips</li><li>Contact</li>
  </ul>

  <h4 style="left:655px;top:38px">CONTACT</h4>
  <ul class="contact-list" style="top:80px">
    <li><svg width="10" height="14" viewBox="0 0 10 14"><path d="M5 0 A5 5 0 0 1 10 5 C10 8 5 14 5 14 C5 14 0 8 0 5 A5 5 0 0 1 5 0 Z" fill="#fff"/><circle cx="5" cy="5" r="2" fill="#000"/></svg><span>LOREM IPSUM DOLOR<br>SIT AMET</span></li>
    <li><svg width="12" height="12" viewBox="0 0 12 12"><path d="M2 0 L4.5 0 L5.5 3 L4 4.5 Q5 7 7.5 8 L9 6.5 L12 7.5 L12 10 Q12 12 10 12 Q0 11 0 2 Q0 0 2 0 Z" fill="#fff"/></svg><span>188-555-0142</span></li>
    <li><svg width="14" height="11" viewBox="0 0 14 11"><rect x="0.75" y="0.75" width="12.5" height="9.5" fill="none" stroke="#fff" stroke-width="1.5"/><path d="M1 1 L7 6 L13 1" fill="none" stroke="#fff" stroke-width="1.5"/></svg><span>hello@maplenbrook.com.au</span></li>
  </ul>

  <h4 style="left:914px;top:38px">FOLLOW US</h4>
  <div class="social"><span></span><span></span><span></span></div>
  <h4 style="left:916px;top:133px">PEST LICENCE</h4>
  <p class="licence">4810362</p>

  <div class="footer-rule"></div>
  <p class="copyright">© 2021 Maple n Brook All Rights Reserved</p>
</footer>

</body>
</html>
```